Brightmill Data Works

Our company is about IT hardwares and IT solutions. IT hardware such as PC, RAMS, storage and servers. IT solutions such as project management, BA. We are also selling new technology too.

Target Market(s)

Consumer, Small to Medium Business, Corporate

Requirements
Must have
• The business card must have the following:
• Name:
• Title:
• Contact Number:
• Email address:
• Website:
• Color: Must match the logo color upgrade

```html
<!DOCTYPE html>
<html lang="en">
<head>
<meta charset="utf-8">
<title>Brightmill Data Works — Business Card</title>
<link href="https://fonts.googleapis.com/css2?family=Saira:wght@300;400;600&display=swap" rel="stylesheet">
<style>
  :root {
    --page-bg: #e6e0d8;
    --card-light: #b8714f;
    --card-mid: #9c4a28;
    --card-deep: #86341a;
    --card-edge: rgba(255, 240, 230, 0.7);
    --brand-ink: #2f2a28;
    --text-light: #f1e4dc;
    --text-soft: #e8d6cc;
    --icon-tile: #e9dcd4;
    --icon-ink: #8a4226;
  }
  * { box-sizing: border-box; margin: 0; padding: 0; }
  html, body {
    width: 1200px; height: 970px; overflow: hidden;
    background: var(--page-bg);
  }
  .canvas {
    position: relative; width: 1200px; height: 970px;
    font-family: "Saira", sans-serif;
  }
  .card {
    position: absolute; left: 100px; top: 207px;
    width: 1000px; height: 555px; border-radius: 36px;
    overflow: hidden;
    border: 2px solid var(--card-edge);
    background:
      radial-gradient(ellipse 420px 300px at 18% 62%, rgba(205,130,95,0.55), transparent 70%),
      linear-gradient(100deg, var(--card-light) 0%, var(--card-mid) 55%, var(--card-deep) 100%);
    box-shadow: 0 20px 40px rgba(60, 30, 15, 0.25);
  }
  .card-curves { position: absolute; inset: 0; }
  .brand {
    position: absolute; left: 0; right: 0; top: 150px;
    display: flex; align-items: center; justify-content: center; gap: 16px;
  }
  .brand-dot {
    width: 26px; height: 26px; border-radius: 50%;
    background: var(--brand-ink);
  }
  .brand-name {
    font-weight: 600; font-size: 44px; letter-spacing: 1px;
    color: var(--brand-ink); text-transform: uppercase;
  }
  .holder {
    position: absolute; left: 66px; top: 340px;
    color: var(--text-light); text-transform: uppercase;
  }
  .holder-name { font-weight: 400; font-size: 34px; line-height: 1.1; letter-spacing: 1px; }
  .holder-title { font-weight: 300; font-size: 28px; line-height: 1.15; color: var(--text-soft); }
  .contacts {
    position: absolute; right: 62px; top: 345px;
    list-style: none; display: flex; flex-direction: column; gap: 14px;
  }
  .contact {
    display: flex; align-items: center; justify-content: flex-end; gap: 18px;
    font-weight: 300; font-size: 26px; letter-spacing: 1px;
    color: var(--text-soft); line-height: 1;
  }
  .contact-icon { width: 30px; height: 30px; flex: none; }
</style>
</head>
<body>
<main class="canvas">
  <section class="card" aria-label="Business card">
    <svg class="card-curves" viewBox="0 0 1000 555" preserveAspectRatio="none" aria-hidden="true">
      <path d="M520 555 C700 470 860 390 1000 300" stroke="rgba(255,190,140,0.18)" stroke-width="2" fill="none"/>
      <path d="M620 555 C760 500 900 450 1000 420 L1000 555 Z" fill="rgba(200,110,40,0.22)"/>
    </svg>

    <div class="brand">
      <span class="brand-dot"></span>
      <span class="brand-name">Brightmill Data Works</span>
    </div>

    <div class="holder">
      <p class="holder-name">Mara Ellison</p>
      <p class="holder-title">Manager</p>
    </div>

    <ul class="contacts">
      <li class="contact">
        <span>+1-555-014-2093</span>
        <svg class="contact-icon" viewBox="0 0 30 30" aria-hidden="true">
          <rect width="30" height="30" rx="3" fill="var(--icon-tile)"/>
          <path d="M10 7 l4 0 l1 5 l-2.5 1.5 c1 2.5 2.5 4 5 5 l1.5 -2.5 l5 1 l0 4 c-9 1 -15 -5 -14 -14 z" fill="var(--icon-ink)"/>
        </svg>
      </li>
      <li class="contact">
        <span>mara@brightmilldata.com</span>
        <svg class="contact-icon" viewBox="0 0 30 30" aria-hidden="true">
          <rect width="30" height="30" rx="3" fill="var(--icon-tile)"/>
          <rect x="6" y="9" width="18" height="12" fill="none" stroke="var(--icon-ink)" stroke-width="1.8"/>
          <path d="M6 9 L15 16 L24 9 M6 21 L12 15 M24 21 L18 15" fill="none" stroke="var(--icon-ink)" stroke-width="1.5"/>
        </svg>
      </li>
      <li class="contact">
        <span>www.brightmilldata.com</span>
        <svg class="contact-icon" viewBox="0 0 30 30" aria-hidden="true">
          <rect width="30" height="30" rx="3" fill="var(--icon-tile)"/>
          <circle cx="15" cy="15" r="9" fill="none" stroke="var(--icon-ink)" stroke-width="1.8"/>
          <ellipse cx="15" cy="15" rx="4" ry="9" fill="none" stroke="var(--icon-ink)" stroke-width="1.3"/>
          <path d="M6 15 H24 M8 10.5 H22 M8 19.5 H22" stroke="var(--icon-ink)" stroke-width="1.3"/>
        </svg>
      </li>
    </ul>
  </section>
</main>
</body>
</html>
```